ecommerce news podcast artwork

Podcast cover art for a podcast featuring daily news and events around ecommerce product businesses.

text to be: BRISK LOOP
optional third line of text with smaller font: Podcast

looking for something that pops with a medium to light blue background. text can be in white/red/orange colors. prefer solid colors for text, but background can vary.
I'm really open to other ideas too, sometimes you don't know what you want until you see it.

Target Market(s)

ecommerce business owners, managers

Industry/Entity Type

news, business, ecommerce

Font styles to use
Sans Serif

Colors
0054AA
0677BA
7BADD7
CADEEF
E8F1F8
0094D4
00A9DD
6FCCEA
C7EBF8
E9F6FB
F0912C
F2A743
F7CA91
FBE8D2
FDF5EE
EB3D1F
EC4F4E
F09395
F8D3D4
FCEDEE

Requirements
Must have
• text: BRISK LOOP
Should not have
• no microphones, headsets/headphones, speakers, or other props like that.

```html
<!DOCTYPE html>
<html lang="en">
<head>
<meta charset="utf-8">
<title>Brisk Loop Podcast Cover</title>
<link rel="stylesheet" href="https://fonts.googleapis.com/css2?family=Roboto:wght@500;700;900&display=swap">
<style>
  :root {
    --page-bg: #7a7a7a;
    --cover-blue: #84dcec;
    --frame-white: #ffffff;
    --headline-red: #ff101f;
    --tag-text: #84dcec;
  }
  html, body {
    margin: 0;
    padding: 0;
    width: 1200px;
    height: 904px;
    overflow: hidden;
    background: var(--page-bg);
  }
  .canvas {
    position: relative;
    width: 1200px;
    height: 904px;
  }
  .cover {
    position: absolute;
    left: 180px;
    top: 32px;
    width: 840px;
    height: 840px;
    background: var(--cover-blue);
  }
  .cover-art {
    display: block;
    width: 840px;
    height: 840px;
  }
  .cover-frame {
    fill: none;
    stroke: var(--frame-white);
    stroke-width: 3;
  }
  .headline {
    font-family: "Roboto", sans-serif;
    font-weight: 900;
    font-size: 224px;
    fill: var(--headline-red);
    letter-spacing: -2px;
  }
  .tag-box {
    fill: var(--headline-red);
  }
  .tag-label {
    font-family: "Roboto", sans-serif;
    font-weight: 500;
    font-size: 58px;
    fill: var(--tag-text);
  }
</style>
</head>
<body>
  <main class="canvas">
    <section class="cover" aria-label="Brisk Loop podcast cover">
      <svg class="cover-art" viewBox="0 0 840 840" xmlns="http://www.w3.org/2000/svg">
        <rect class="cover-frame" x="23" y="24" width="794" height="792"/>
        <text class="headline" x="112" y="362">BRISK</text>
        <text class="headline" x="112" y="555">LOOP</text>
        <rect class="tag-box" x="443" y="576" width="280" height="66"/>
        <text class="tag-label" x="583" y="630" text-anchor="middle">PODCAST</text>
      </svg>
    </section>
  </main>
</body>
</html>
```